Coralbay Yardcraft need a flyer - A6 - Double sided

We need a flyer that will engage potential customer in need for gardening services. We offer high quality gardening services spanning from lawn mowing and weeding to soil improvement to tree pruning and so on.
I would like a double sided flyer A6 size. I trust your expert touch in terms of lay out but the general idea I had was to have one side with the logo, a catchy picture (or more), the website/phone number/address and on the flip side a little more text focusing on the client perspective with statement such as 'Let us do the hard work so that you can enjoy your garden' (obviously the wording isn't my strongest skill) but the idea is to get into the customer perspective;
I would also like to list all the service we can offer such as but not limited to weeding, pruning, lawn care, green waste disposal, soil improvement, hedging, edging, lawn mowing,...
Happy for you to use any picture free of right from the internet if necessary

Target Market(s)

Home owner & Businesses

Industry/Entity Type

Landscape Gardening

Requirements
Must have
• website - http://yardcraft-coralbay.example.au (feel free to browse the website to get ideas on color theme and overall look)
• phone number - (08) 6193 4071
Nice to have
• a list of services on offer
• phone number and website
• being customer perspective focused (the benefits for the customer) - perhaps on the flip side some text like 'highly trained and experienced landscape gardeners so that the job is done perfectly every time', 'always carrying all range of commercial grade tools so that we can tackle any job', 'Experienced gardeners so that the job is achieve faster' (it doesn't have to be in those exact words as I trust that you may be expert in wording as well as designers?)

```html
<!DOCTYPE html>
<html lang="en">
<head>
<meta charset="utf-8">
<title>Coralbay Yardcraft – A6 Flyer</title>
<link rel="stylesheet" href="https://fonts.googleapis.com/css2?family=Open+Sans:wght@400;600;700;800&display=swap">
<style>
  :root {
    --page-bg: #e6e4e1;
    --charcoal: #3a3f3d;
    --charcoal-dark: #333836;
    --leaf-green: #7cb83e;
    --white: #ffffff;
    --list-text: #4a4f4d;
    --blossom: #d98aa6;
    --meadow: #8fbf5a;
    --meadow-deep: #5f8f3a;
    --hammock-yellow: #d9d84a;
  }
  * { box-sizing: border-box; margin: 0; padding: 0; }
  html, body {
    width: 946px; height: 1200px; overflow: hidden;
    background: var(--page-bg);
    font-family: "Open Sans", Arial, sans-serif;
  }
  .flyer-side {
    position: absolute;
    width: 745px; height: 528px;
    background: var(--white);
    box-shadow: 0 6px 16px rgba(0,0,0,0.25);
    overflow: hidden;
  }
  .flyer-front { left: 64px; top: 48px; }
  .flyer-back  { left: 152px; top: 614px; }

  /* Front */
  .front-photo {
    position: absolute; left: 0; top: 0; width: 745px; height: 474px;
    background:
      radial-gradient(ellipse at 30% 10%, rgba(217,138,166,0.85), rgba(217,138,166,0) 45%),
      radial-gradient(ellipse at 85% 15%, rgba(217,138,166,0.8), rgba(217,138,166,0) 40%),
      linear-gradient(180deg, #a7c98a 0%, var(--meadow) 55%, var(--meadow-deep) 100%);
  }
  .brand-name {
    position: absolute; left: 0; right: 0; top: 188px;
    text-align: center;
    color: var(--charcoal);
    font-weight: 800;
    line-height: 0.92;
    text-transform: uppercase;
  }
  .brand-name .line-1 { display: block; font-size: 74px; letter-spacing: -1px; }
  .brand-name .line-2 { display: block; font-size: 54px; letter-spacing: 1px; }
  .brand-mark {
    display: inline-block; width: 22px; height: 22px;
    background: var(--charcoal); border-radius: 50%;
    vertical-align: middle; margin-right: 12px; position: relative; top: -6px;
  }
  .front-tagline {
    position: absolute; left: 0; right: 0; top: 380px;
    text-align: center; color: var(--white);
    font-size: 24px; font-weight: 700; line-height: 1.3;
    text-shadow: 0 1px 3px rgba(0,0,0,0.55);
  }

  /* Contact bar */
  .contact-bar {
    position: absolute; left: 0; bottom: 0; width: 100%; height: 54px;
    background: var(--charcoal);
    color: var(--white);
    display: flex; align-items: center;
    padding: 0 20px 0 32px;
  }
  .contact-bar .website { font-size: 15px; flex: 1; }
  .contact-bar .quote-note { font-size: 15px; margin-right: 18px; }
  .contact-bar .phone {
    display: flex; align-items: center; gap: 8px;
    font-size: 22px; font-weight: 700;
  }
  .contact-bar svg { width: 24px; height: 24px; }

  /* Back */
  .back-headline {
    position: absolute; left: 0; top: 0; width: 100%; height: 70px;
    background: var(--leaf-green);
    color: var(--white);
    display: flex; align-items: center; justify-content: center;
    font-size: 27px; font-weight: 600; text-transform: uppercase;
    letter-spacing: -0.3px;
  }
  .services {
    position: absolute; left: 24px; top: 86px; right: 24px;
  }
  .services-intro {
    display: flex; align-items: center; gap: 12px;
    font-size: 17px; font-weight: 700; color: var(--charcoal-dark);
    margin-bottom: 12px;
  }
  .services-intro svg { width: 22px; height: 22px; }
  .services-list {
    list-style: none;
    display: grid; grid-template-columns: 316px 1fr;
    row-gap: 3px; padding-left: 32px;
    grid-auto-flow: column; grid-template-rows: repeat(4, auto);
  }
  .services-list li {
    font-size: 16.5px; font-weight: 700; color: var(--list-text);
  }
  .services-list li::before { content: "» "; }
  .back-photo {
    position: absolute; left: 0; top: 245px; width: 100%; height: 229px;
    background:
      linear-gradient(170deg, rgba(217,216,74,0.0) 30%, rgba(217,216,74,0.75) 50%, rgba(124,184,62,0.7) 65%, rgba(124,184,62,0) 80%),
      linear-gradient(180deg, #9dbb7a 0%, #6f9a4c 60%, #52773a 100%);
  }
</style>
</head>
<body>

<section class="flyer-side flyer-front">
  <div class="front-photo" role="img" aria-label="Garden photo with pink blossom branches above a soft green lawn and a wheelbarrow"></div>
  <h1 class="brand-name">
    <span class="line-1"><span class="brand-mark"></span>Coralbay</span>
    <span class="line-2">Yardcraft</span>
  </h1>
  <p class="front-tagline">Reliable, affordable gardening<br>services in Perth</p>
  <footer class="contact-bar">
    <span class="website">www.yardcraft-coralbay.example.au</span>
    <span class="quote-note">Call today for your FREE QUOTE</span>
    <span class="phone">
      <svg viewBox="0 0 24 24" aria-hidden="true"><circle cx="12" cy="12" r="10.5" fill="none" stroke="#fff" stroke-width="1.6"/><path d="M8.6 6.8l1.8-.4 1.1 2.6-1.2 1c.6 1.4 1.6 2.4 3 3l1-1.2 2.6 1.1-.4 1.8c-.2.6-.7.9-1.3.9-4.2-.3-7.6-3.7-7.9-7.9 0-.6.3-1.1.9-1.3z" fill="#fff"/></svg>
      (08) 6193 4071
    </span>
  </footer>
</section>

<section class="flyer-side flyer-back">
  <h2 class="back-headline">Sit back and relax, we'll take it from here</h2>
  <div class="services">
    <p class="services-intro">
      <svg viewBox="0 0 22 22" aria-hidden="true"><circle cx="11" cy="11" r="10" fill="var(--charcoal-dark)"/><path d="M8.5 6.5l6 4.5-6 4.5z" fill="#fff"/></svg>
      We provide many services including:
    </p>
    <ul class="services-list">
      <li>Lawn Care</li>
      <li>Tree pruning &amp; Plant Care</li>
      <li>Hedge trimming</li>
      <li>Organic Gardening</li>
      <li>Mulching</li>
      <li>Weed Control</li>
      <li>Rubbish &amp; Green Waste Removal</li>
      <li>Fertilising &amp; Soil Improvement</li>
    </ul>
  </div>
  <div class="back-photo" role="img" aria-label="Photo of a family relaxing in a striped green and yellow hammock in a leafy garden"></div>
  <footer class="contact-bar">
    <span class="website">www.yardcraft-coralbay.example.au</span>
    <span class="quote-note">Call today for your FREE QUOTE</span>
    <span class="phone">
      <svg viewBox="0 0 24 24" aria-hidden="true"><circle cx="12" cy="12" r="10.5" fill="none" stroke="#fff" stroke-width="1.6"/><path d="M8.6 6.8l1.8-.4 1.1 2.6-1.2 1c.6 1.4 1.6 2.4 3 3l1-1.2 2.6 1.1-.4 1.8c-.2.6-.7.9-1.3.9-4.2-.3-7.6-3.7-7.9-7.9 0-.6.3-1.1.9-1.3z" fill="#fff"/></svg>
      (08) 6193 4071
    </span>
  </footer>
</section>

</body>
</html>
```